Business Cards for a law firm

Business cards for our law firm. Use our silhoette logo and OAK PARTNERS - check our website (www.oakpartners.example)

Contact Information for Business Card

our silhouette logo, OAK PARTNERS, 800-555-0147, Dorian Pemberton, dorian@oakpartners.example

Requirements
Must have
• our silhouette logo, OAK PARTNERS, 800-555-0147, Dorian Pemberton, dorian@oakpartners.example

```html
<!DOCTYPE html>
<html lang="en">
<head>
<meta charset="utf-8">
<title>Oak Partners – Business Cards</title>
<link rel="stylesheet" href="https://fonts.googleapis.com/css2?family=Poppins:wght@400;500;600&display=swap">
<style>
  :root {
    --navy: #182a5e;
    --gold: #eba421;
    --white: #ffffff;
    --ink: #1c1c1c;
    --backdrop: #d8d8d8;
  }
  * { margin: 0; padding: 0; box-sizing: border-box; }
  html, body { width: 960px; height: 1200px; overflow: hidden; }
  body {
    background: var(--backdrop);
    font-family: "Poppins", sans-serif;
    position: relative;
  }
  .card {
    position: absolute;
    left: 100px;
    width: 760px;
    height: 434px;
    border-radius: 24px;
    overflow: hidden;
    background: var(--white);
    box-shadow: 0 10px 28px rgba(0,0,0,0.12);
  }
  .card-front { top: 120px; }
  .card-back { top: 646px; }
  .card-shapes { position: absolute; inset: 0; width: 100%; height: 100%; }

  /* Front */
  .front-brand {
    position: absolute;
    left: 190px; right: 110px; top: 0; bottom: 0;
    display: flex; flex-direction: column; align-items: center; justify-content: center;
    gap: 34px;
  }
  .brand-dot {
    width: 96px; height: 96px; border-radius: 50%;
    background: var(--navy);
  }
  .brand-name {
    font-weight: 600;
    font-size: 50px;
    letter-spacing: 5px;
    color: var(--navy);
    white-space: nowrap;
  }

  /* Back */
  .back-brand {
    position: absolute;
    left: 530px; right: 0; top: 0; bottom: 0;
    display: flex; flex-direction: column; align-items: center; justify-content: center;
    gap: 22px;
  }
  .back-brand .brand-dot { width: 64px; height: 64px; background: var(--white); }
  .back-brand .brand-name { font-size: 20px; font-weight: 500; letter-spacing: 3px; color: var(--white); }

  .contact-block { position: absolute; left: 56px; top: 62px; }
  .person-name {
    font-weight: 500;
    font-size: 34px;
    letter-spacing: 1px;
    text-transform: uppercase;
    color: var(--navy);
    line-height: 1;
  }
  .person-name .surname { color: var(--gold); }
  .name-rule { display: flex; margin-top: 10px; height: 5px; width: 300px; }
  .name-rule .rule-navy { flex: 0 0 118px; background: var(--navy); }
  .name-rule .rule-gold { flex: 1; background: var(--gold); }

  .contact-list { list-style: none; margin-top: 38px; }
  .contact-list li {
    display: flex; align-items: center; gap: 22px;
    font-size: 21px; color: var(--ink);
    height: 48px;
  }
  .contact-icon { width: 24px; height: 24px; flex: 0 0 24px; }
</style>
</head>
<body>

  <section class="card card-front" aria-label="Business card front">
    <svg class="card-shapes" viewBox="0 0 760 434" aria-hidden="true">
      <path d="M0 0 H150 C80 120 70 300 96 434 H0 Z" fill="var(--navy)"/>
      <path d="M150 0 C80 120 70 300 96 434 H134 C104 300 120 140 196 0 Z" fill="var(--gold)"/>
      <path d="M660 0 H760 V320 Z" fill="var(--navy)"/>
    </svg>
    <div class="front-brand">
      <span class="brand-dot"></span>
      <span class="brand-name">OAK PARTNERS</span>
    </div>
  </section>

  <section class="card card-back" aria-label="Business card back">
    <svg class="card-shapes" viewBox="0 0 760 434" aria-hidden="true">
      <path d="M0 434 H110 L0 330 Z" fill="var(--navy)"/>
      <path d="M500 0 C466 130 474 300 530 434 H760 V0 Z" fill="var(--navy)"/>
      <path d="M466 0 C420 140 440 320 496 434 H530 C474 300 466 130 500 0 Z" fill="var(--gold)"/>
    </svg>

    <div class="back-brand">
      <span class="brand-dot"></span>
      <span class="brand-name">OAK PARTNERS</span>
    </div>

    <div class="contact-block">
      <h1 class="person-name">Dorian <span class="surname">Pemberton</span></h1>
      <div class="name-rule"><span class="rule-navy"></span><span class="rule-gold"></span></div>

      <ul class="contact-list">
        <li>
          <svg class="contact-icon" viewBox="0 0 24 24" aria-hidden="true"><path d="M6.6 10.8a15 15 0 0 0 6.6 6.6l2.2-2.2c.3-.3.7-.4 1-.2 1.1.4 2.3.6 3.6.6.6 0 1 .4 1 1V20c0 .6-.4 1-1 1A17 17 0 0 1 3 4c0-.6.4-1 1-1h3.5c.6 0 1 .4 1 1 0 1.3.2 2.5.6 3.6.1.3 0 .7-.2 1z" fill="var(--gold)"/></svg>
          <span>800-555-0147</span>
        </li>
        <li>
          <svg class="contact-icon" viewBox="0 0 24 24" aria-hidden="true"><rect x="2" y="5" width="20" height="14" rx="1.5" fill="var(--gold)"/><path d="M3 6l9 7 9-7" stroke="var(--white)" stroke-width="1.6" fill="none"/></svg>
          <span>dorian@oakpartners.example</span>
        </li>
        <li>
          <svg class="contact-icon" viewBox="0 0 24 24" aria-hidden="true"><g fill="none" stroke="var(--gold)" stroke-width="1.8"><circle cx="12" cy="12" r="9.5"/><ellipse cx="12" cy="12" rx="4" ry="9.5"/><path d="M2.5 12h19M4 7h16M4 17h16"/></g></svg>
          <span>www.oakpartners.example</span>
        </li>
        <li>
          <svg class="contact-icon" viewBox="0 0 24 24" aria-hidden="true"><path d="M12 2a7 7 0 0 0-7 7c0 5 7 13 7 13s7-8 7-13a7 7 0 0 0-7-7z" fill="var(--gold)"/><circle cx="12" cy="9" r="2.6" fill="var(--white)"/></svg>
          <span>Available 24/7</span>
        </li>
      </ul>
    </div>
  </section>

</body>
</html>
```